A Kettle for Distant Orchards

I want the title to look like it’s painted with a paintbrush. This is also a story about my relationship with a spirit of a famous Venetian painter from the 1800s so paint references and swirls are encouraged. The story takes place in Chicago; Bali; Venice, Italy; Sedona, Arizona; and Paris, France. Venice is the most important place. I attached a photo that may make a good cover photo

Target Market(s)

For those interested in travel, spirituality, healing

Requirements
Must have
• The title should look like it’s painted and be flowy
Nice to have
• Story takes place in Venice Italy. Any Venice symbolism would be great

```html
<!DOCTYPE html>
<html lang="en">
<head>
<meta charset="utf-8">
<title>A Kettle for Distant Orchards – Cover Wrap</title>
<link rel="stylesheet" href="https://fonts.googleapis.com/css2?family=Caveat+Brush&family=Jost:wght@400&family=Montserrat:wght@400&family=Permanent+Marker&display=block">
<style>
  :root {
    --canvas: #ffffff;
    --cover: #000000;
    --ink: #f2f2f2;
    --spine-edge: #151515;
    --stone-light: #d9cdb9;
    --stone-mid: #a89580;
    --water-light: #8fb3a8;
    --water-deep: #4f7a72;
  }
  * { box-sizing: border-box; margin: 0; padding: 0; }
  html, body { width: 1200px; height: 1200px; overflow: hidden; background: var(--canvas); }
  .wrap {
    position: absolute; left: 139px; top: 28px;
    width: 928px; height: 640px;
    background: var(--cover); color: var(--ink);
    display: flex;
  }
  .panel { position: relative; height: 100%; }
  .back { width: 428px; }
  .spine { width: 73px; border-left: 1px solid var(--spine-edge); border-right: 1px solid var(--spine-edge); }
  .front { width: 427px; }

  .brush-title {
    font-family: "Permanent Marker", "Caveat Brush", cursive;
    text-transform: uppercase;
    text-align: center;
    font-weight: 400;
    font-style: normal;
    transform: skewX(-8deg);
    letter-spacing: -0.5px;
  }
  .back .brush-title {
    position: absolute; left: 0; right: 0; top: 66px;
    font-size: 28px; line-height: 36px;
  }
  .blurb {
    position: absolute; left: 26px; width: 368px;
    font-family: "Montserrat", sans-serif;
    font-size: 10.6px; line-height: 15.8px;
    text-align: justify; text-align-last: center;
  }
  .blurb-one { top: 190px; }
  .blurb-two { top: 332px; }

  .spine-text {
    position: absolute; left: 50%; top: 36px;
    transform-origin: 0 0;
    transform: rotate(90deg) translateY(-50%);
    display: flex; align-items: center; gap: 26px;
    white-space: nowrap;
  }
  .spine-title {
    font-family: "Permanent Marker", "Caveat Brush", cursive;
    text-transform: uppercase; font-size: 18px;
    display: inline-block; transform: skewX(-8deg);
  }
  .spine-author { font-family: "Jost", sans-serif; font-size: 18px; letter-spacing: 1px; }

  .front .brush-title {
    position: absolute; left: 0; right: 0; top: 46px;
    font-size: 44px; line-height: 66px;
  }
  .cover-art { position: absolute; left: 7px; top: 262px; width: 415px; height: 315px; }
  .author {
    position: absolute; left: 0; right: 0; top: 580px;
    font-family: "Jost", sans-serif; font-size: 27px; letter-spacing: 0.5px;
    text-align: center;
  }
</style>
</head>
<body>
<main class="wrap">
  <section class="panel back">
    <h2 class="brush-title">A Kettle for<br>Distant<br>Orchards</h2>
    <p class="blurb blurb-one">Lorem ipsum dolor sit amet, consectetur adipiscing elit, sed do eiusmod tempor incididunt ut labore et dolore magna aliqua. Quis ipsum suspendisse ultrices gravida. Risus commodo viverra maecenas accumsan lacus vel facilisis. Lorem ipsum dolor sit amet, consectetur adipiscing elit, sed do eiusmod tempor incididunt ut labore et dolore magna aliqua. Quis ipsum suspendisse ultrices gravida. Risus commodo viverra maecenas accumsan lacus vel facilisis.</p>
    <p class="blurb blurb-two">Lorem ipsum dolor sit amet, consectetur adipiscing elit, sed do eiusmod tempor incididunt ut labore et dolore magna aliqua. Quis ipsum suspendisse ultrices gravida. Risus commodo viverra maecenas accumsan lacus vel facilisis. Lorem ipsum dolor sit amet, consectetur adipiscing elit, sed do eiusmod tempor incididunt ut labore et dolore magna aliqua. Quis ipsum suspendisse ultrices gravida. Risus commodo viverra maecenas accumsan lacus vel facilisis. Lorem ipsum dolor sit amet, consectetur adipiscing elit, sed do eiusmod tempor incididunt ut labore et dolore magna aliqua. Quis ipsum suspendisse ultrices gravida. Risus commodo viverra maecenas accumsan lacus vel facilisis.</p>
  </section>

  <section class="panel spine">
    <div class="spine-text">
      <span class="spine-title">A Kettle for Distant Orchards</span>
      <span class="spine-author">AUTHOR NAME</span>
    </div>
  </section>

  <section class="panel front">
    <h1 class="brush-title">A Kettle for<br>Distant<br>Orchards</h1>
    <svg class="cover-art" viewBox="0 0 415 315" role="img" aria-label="Painterly brush-stroke framed view of a Venetian canal with an arched stone footbridge between weathered buildings">
      <defs>
        <linearGradient id="canal-tones" x1="0" y1="0" x2="0" y2="1">
          <stop offset="0" stop-color="var(--stone-light)"/>
          <stop offset="0.45" stop-color="var(--stone-mid)"/>
          <stop offset="0.62" stop-color="var(--water-light)"/>
          <stop offset="1" stop-color="var(--water-deep)"/>
        </linearGradient>
      </defs>
      <path fill="url(#canal-tones)" d="M40 70 L95 30 L120 45 L150 10 L190 35 L230 20 L265 40 L300 0 L330 25 L370 60 L395 110 L410 135 L395 160 L385 220 L350 240 L325 270 L290 285 L245 295 L195 310 L170 300 L130 270 L95 240 L60 230 L20 220 L15 180 L0 140 L25 120 Z"/>
    </svg>
    <p class="author">AUTHOR NAME</p>
  </section>
</main>
</body>
</html>
```